Business Card Brantley Digital

Design of two business cards (board) for Brantley Digital. Brantley Digital DMCC, based in in Dubai U.A.E. Brantley Digital is a self-contained online company, taking an online concept from idea to reality. Concretely, this has involved the (partly remote) management, website development, market implementation and mobile application development for several platforms.

Frontside of business card should feature our company logo (Brantley) and personal details. Backside should feature the logo's of our current brands (mendupnow, getsetdone and gatherguide). We would prefer a design based on the grey/orange color scheme of our company. Brantley Digital is a young, modern and dynamic company and we would like to see this reflected in the design.

Industry/Entity Type

Business

```html
<!DOCTYPE html>
<html lang="en">
<head>
<meta charset="UTF-8">
<title>Brantley Digital – Business Card</title>
<link rel="stylesheet" href="https://fonts.googleapis.com/css2?family=Lato:wght@400;700&display=swap">
<style>
  :root {
    --backdrop: #d9d9d9;
    --card: #ffffff;
    --ink: #4d4d4f;
    --ink-dark: #262626;
    --accent: #ef4a23;
  }
  * { margin: 0; padding: 0; box-sizing: border-box; }
  html, body { width: 992px; height: 1200px; overflow: hidden; }
  body {
    background: var(--backdrop);
    font-family: "Lato", sans-serif;
    position: relative;
  }
  .card {
    position: absolute;
    background: var(--card);
  }
  .card--front { left: 74px; top: 61px; width: 863px; height: 501px; }
  .card--back  { left: 72px; top: 636px; width: 866px; height: 505px; }

  .brand-mark {
    position: absolute;
    left: 0; right: 0; top: 220px;
    text-align: center;
    font-weight: 700;
    font-size: 68px;
    letter-spacing: 1px;
    color: var(--ink-dark);
  }

  .person { position: absolute; left: 111px; top: 100px; }
  .person__name {
    font-size: 39px;
    line-height: 1;
    color: var(--ink);
    font-weight: 700;
    letter-spacing: -0.5px;
  }
  .person__name .first { color: var(--accent); font-weight: 400; }
  .person__role {
    margin-top: 8px;
    font-size: 21px;
    color: var(--accent);
  }

  .contacts { position: absolute; left: 102px; top: 288px; list-style: none; }
  .contacts li {
    display: flex;
    align-items: center;
    height: 37px;
    font-size: 18px;
    color: var(--ink);
  }
  .contacts svg { width: 18px; height: 18px; margin-right: 24px; fill: var(--ink-dark); flex: none; }

  .company-name {
    position: absolute;
    left: 560px; width: 250px; top: 318px;
    text-align: center;
    font-size: 37px;
    letter-spacing: 6px;
    color: var(--accent);
    font-weight: 400;
  }
</style>
</head>
<body>
  <section class="card card--front" aria-label="Card front">
    <div class="brand-mark">getsetdone</div>
  </section>

  <section class="card card--back" aria-label="Card back">
    <div class="person">
      <h1 class="person__name"><span class="first">YOUR</span> NAME</h1>
      <p class="person__role">Director</p>
    </div>

    <ul class="contacts">
      <li>
        <svg viewBox="0 0 24 24" aria-hidden="true"><path d="M2 7c0-2 3-4 10-4s10 2 10 4v2h-5V7H7v2H2zM6 11h12l3 9H3z M12 13a3 3 0 1 0 0 6a3 3 0 1 0 0-6z"/></svg>
        + 000 - 1234 - 5678
      </li>
      <li>
        <svg viewBox="0 0 24 24" aria-hidden="true"><path d="M2 5h20v14H2z M3.5 6.5 12 13l8.5-6.5v-.1h-17z" fill-rule="evenodd"/></svg>
        admin@your e-mail.com
      </li>
      <li>
        <svg viewBox="0 0 24 24" aria-hidden="true"><path d="M10 14a5 5 0 0 1 0-7l3-3a5 5 0 0 1 7 7l-2 2-1.5-1.5 2-2a3 3 0 0 0-4-4l-3 3a3 3 0 0 0 0 4zM14 10a5 5 0 0 1 0 7l-3 3a5 5 0 0 1-7-7l2-2 1.5 1.5-2 2a3 3 0 0 0 4 4l3-3a3 3 0 0 0 0-4z"/></svg>
        your web site.com
      </li>
      <li>
        <svg viewBox="0 0 24 24" aria-hidden="true"><path d="M12 2 1 12h3v10h6v-6h4v6h6V12h3z"/></svg>
        000 Seventh Avenue, New York 12345
      </li>
    </ul>

    <div class="company-name">BRANTLEY</div>
  </section>
</body>
</html>
```